Wealth Education Business Needs Sharp Business Card Design

We need a business card design for a recently launched investor education business called Harbor Crest.

The final design should promote security, empowerment, self improvement and financial gain. The card will ideally promote the stature of the business.

For more information and colours please visit harborcrest.com.au

Target Market(s)

Corporate executives and high net worth individuals

Industry/Entity Type

Education

Contact Information for Business Card

```html
<!DOCTYPE html>
<html lang="en">
<head>
<meta charset="utf-8">
<title>Harbor Crest – Business Card</title>
<link rel="stylesheet" href="https://fonts.googleapis.com/css2?family=Lato:wght@400;700&display=swap">
<style>
  :root {
    --page-bg: #e9e7e3;
    --card-bg: #f3f5f4;
    --leaf-green: #9fcb6a;
    --pale: #f1f4f2;
    --soft-teal: #a9c9c6;
    --ink: #2c2c2c;
    --logo-ink: #3a3634;
    --name-teal: #4a8a96;
    --sand: #9a7f55;
    --icon: #2e6f75;
  }
  * { box-sizing: border-box; margin: 0; padding: 0; }
  html, body {
    width: 1200px; height: 970px; overflow: hidden;
    background: var(--page-bg);
    font-family: "Lato", Arial, sans-serif;
  }
  .card {
    position: absolute; left: 100px; top: 205px;
    width: 1000px; height: 560px;
    border-radius: 26px; overflow: hidden;
    background: var(--card-bg);
    box-shadow: 0 6px 24px rgba(0,0,0,0.12);
  }
  .card-backdrop {
    position: absolute; inset: 0;
    background: linear-gradient(115deg,
      var(--leaf-green) 0%,
      #c4df9f 22%,
      var(--pale) 44%,
      var(--pale) 68%,
      var(--soft-teal) 100%);
  }
  .brand {
    position: absolute; left: 0; right: 0; top: 92px;
    text-align: center;
    font-weight: 700; font-size: 40px; letter-spacing: 7px;
    color: var(--logo-ink);
  }
  .contact-list {
    position: absolute; right: 46px; top: 204px;
    list-style: none; text-align: right;
    font-size: 25px; color: var(--ink); line-height: 34px;
  }
  .contact-list li { display: flex; justify-content: flex-end; align-items: center; gap: 12px; }
  .contact-list .gap { height: 28px; }
  .icon { width: 22px; height: 22px; flex: none; }
  .icon-spacer { width: 22px; flex: none; }
  .person { position: absolute; left: 46px; top: 368px; }
  .person-name { font-weight: 700; font-size: 33px; color: var(--name-teal); }
  .person-role { font-size: 24px; color: var(--ink); margin-top: 2px; }
  .social {
    position: absolute; left: 46px; top: 488px;
    display: flex; align-items: center; gap: 10px;
    font-weight: 700; font-size: 26px; color: var(--sand);
  }
  .social-mark { width: 20px; height: 20px; background: #6b6b6b; border-radius: 3px; }
</style>
</head>
<body>
  <div class="card">
    <div class="card-backdrop" role="img" aria-label="Flowing green, blue and teal decorative swoosh bands across the card"></div>

    <div class="brand">HARBOR CREST</div>

    <ul class="contact-list">
      <li>1300 555 018
        <svg class="icon" viewBox="0 0 24 24"><path fill="var(--icon)" d="M3 9c0-3 4-5 9-5s9 2 9 5l-3 2-3-2V7H9v2l-3 2zM6 13h12l2 7H4z"/></svg>
      </li>
      <li>+613 9555 0142
        <svg class="icon" viewBox="0 0 24 24"><rect x="6" y="2" width="12" height="20" rx="2" fill="none" stroke="var(--icon)" stroke-width="2"/><circle cx="12" cy="18" r="1.3" fill="var(--icon)"/></svg>
      </li>
      <li>support@harborcrest.com.au
        <svg class="icon" viewBox="0 0 24 24"><rect x="2" y="5" width="20" height="14" rx="1" fill="var(--icon)"/><path d="M3 6l9 7 9-7" fill="none" stroke="#fff" stroke-width="1.8"/></svg>
      </li>
      <li>www.harborcrest.com.au
        <svg class="icon" viewBox="0 0 24 24"><g fill="none" stroke="var(--icon)" stroke-width="1.8"><circle cx="12" cy="12" r="9.5"/><ellipse cx="12" cy="12" rx="4" ry="9.5"/><path d="M2.5 12h19M4 7h16M4 17h16"/></g></svg>
      </li>
      <li class="gap"></li>
      <li>Level 4, 72 Quayside Row
        <svg class="icon" viewBox="0 0 24 24"><path fill="var(--icon)" d="M12 3 2 12h3v9h5v-6h4v6h5v-9h3z"/></svg>
      </li>
      <li>Southbank VIC 3006 <span class="icon-spacer"></span></li>
    </ul>

    <div class="person">
      <div class="person-name">Mara Ellison</div>
      <div class="person-role">Director</div>
    </div>

    <div class="social">Find Us On <span class="social-mark"></span></div>
  </div>
</body>
</html>
```